Business Card & Letterhead Design

We a financial advice company based in Australia. We provide advice to wealthy farmers.

We are changing our business name FROM Brightvale Financial TO Tallowmere Wealth and we need a new letterhead and double sided business card design

Attached is designs from our previous branding (Brightvale Financial) as it includes all the details we require on the new Tallowmere Wealth business cards and letterhead.

Need extra days to review

```html
<!DOCTYPE html>
<html lang="en">
<head>
<meta charset="utf-8">
<title>Tallowmere Wealth — Stationery</title>
<link href="https://fonts.googleapis.com/css2?family=Cinzel:wght@400;700&family=Montserrat:wght@400&family=Roboto:wght@400&display=swap" rel="stylesheet">
<style>
:root{
  --stage:#999999;
  --paper:#f7f7f5;
  --charcoal:#3d3d3d;
  --ink:#444444;
  --faint:#ebebe9;
  --tab:#6f6f6d;
  --white:#ffffff;
}
*{margin:0;padding:0;box-sizing:border-box}
html,body{width:1200px;height:1032px;overflow:hidden;background:var(--stage)}
.canvas{position:relative;width:1200px;height:1032px}
.brand-name{font-family:"Cinzel",serif;font-weight:400;letter-spacing:.04em;white-space:nowrap}
.tagline{font-family:"Montserrat",sans-serif;letter-spacing:.32em;white-space:nowrap}
.ring{position:absolute;border-radius:50%}

/* letterhead */
.letterhead{position:absolute;left:446px;top:74px;width:626px;height:884px;background:var(--paper);overflow:hidden}
.letterhead .mark{left:86px;top:42px;width:76px;height:76px;border:3px solid var(--ink)}
.letterhead .brand-name{position:absolute;left:34px;top:124px;font-size:16.5px;color:var(--ink)}
.letterhead .tagline{position:absolute;left:50px;top:144px;font-size:6.5px;letter-spacing:.27em;color:var(--ink)}
.letterhead .watermark{left:118px;top:246px;width:392px;height:392px;border:10px solid var(--faint)}
.lh-contacts{position:absolute;left:34px;top:788px;font-family:"Roboto",sans-serif;font-size:11.5px;color:var(--ink)}
.lh-contacts .row{display:flex;align-items:center;gap:6px;height:18px}
.lh-contacts .gap{height:10px}
.lh-contacts svg{width:11px;height:11px;flex:none}
.lh-contacts .sep{margin-left:6px}
.lh-tab{position:absolute;left:382px;top:854px;width:244px;height:30px}
.lh-web{position:absolute;left:432px;top:862px;font-family:"Roboto",sans-serif;font-size:11px;color:var(--white)}

/* business cards */
.card{position:absolute;left:127px;width:271px;overflow:hidden}
.card-front{top:330px;height:163px;background:var(--charcoal)}
.card-front .watermark{left:196px;top:-6px;width:170px;height:170px;border:3px solid #4a4a4a}
.card-front .mark{left:114px;top:46px;width:44px;height:44px;border:2px solid var(--white)}
.card-front .brand-name{position:absolute;left:0;width:100%;text-align:center;top:94px;font-size:13.5px;color:var(--white)}
.card-front .tagline{position:absolute;left:0;width:100%;text-align:center;top:111px;font-size:6px;letter-spacing:.3em;color:#dddddd}

.card-back{top:537px;height:164px;background:var(--paper)}
.card-back .brand-name{position:absolute;left:12px;top:11px;font-size:13.5px;color:var(--ink)}
.card-back .tagline{position:absolute;left:19px;top:28px;font-size:6px;letter-spacing:.3em;color:var(--ink)}
.card-back .band{position:absolute;left:0;top:45px;width:100%;height:96px;background:var(--charcoal)}
.card-back .mark{left:151px;top:42px;width:110px;height:110px;background:var(--white)}
.card-back .mark-inner{left:158px;top:49px;width:96px;height:96px;border:2px solid var(--charcoal);background:var(--white)}
.person{position:absolute;left:9px;top:55px;color:var(--white)}
.person .name{font-family:"Cinzel",serif;font-weight:700;font-size:9px}
.person .role{font-family:"Roboto",sans-serif;font-size:5.5px;line-height:7px;color:#e5e5e5}
.person ul{list-style:none;margin-top:8px;font-family:"Roboto",sans-serif;font-size:5.6px;color:#e5e5e5}
.person li{display:flex;align-items:center;gap:6px;height:9.4px}
.person li svg{width:5px;height:5px;flex:none}
.card-back .address{position:absolute;left:9px;top:147px;display:flex;align-items:center;gap:5px;font-family:"Roboto",sans-serif;font-size:5.5px;color:var(--ink);white-space:nowrap}
.card-back .address svg{width:5px;height:6px}
</style>
</head>
<body>
<div class="canvas">

  <section class="card card-front" aria-label="Business card front">
    <div class="ring watermark"></div>
    <div class="ring mark"></div>
    <div class="brand-name">Tallowmere Wealth</div>
    <div class="tagline">STRATEGIC FINANCIAL ADVICE</div>
  </section>

  <section class="card card-back" aria-label="Business card back">
    <div class="brand-name">Tallowmere Wealth</div>
    <div class="tagline">STRATEGIC FINANCIAL ADVICE</div>
    <div class="band"></div>
    <div class="ring mark"></div>
    <div class="ring mark-inner"></div>
    <div class="person">
      <div class="name">SAM HARTLEY</div>
      <div class="role">B.Ag.Ec. Dip F.P. CFP®<br>Managing Director</div>
      <ul>
        <li><svg viewBox="0 0 10 10"><path d="M1 3h8v2H1z M3 5h4v4H3z" fill="#fff"/></svg>(07) 3200 5814</li>
        <li><svg viewBox="0 0 10 10"><rect x="2" y="0" width="6" height="10" rx="1" fill="#fff"/></svg>(07) 3200 5815</li>
        <li><svg viewBox="0 0 10 10"><rect x="1" y="3" width="8" height="5" fill="#fff"/><rect x="3" y="1" width="4" height="2" fill="#fff"/></svg>0412 608 273</li>
        <li><svg viewBox="0 0 10 10"><rect x="0" y="2" width="10" height="6" fill="#fff"/></svg>sam@brightvalefinancial.com.au</li>
        <li><svg viewBox="0 0 10 10"><circle cx="5" cy="5" r="4.5" fill="#fff"/></svg>www.brightvalefinancial.com.au</li>
      </ul>
    </div>
    <div class="address"><svg viewBox="0 0 10 12"><path d="M5 0a4 4 0 0 1 4 4c0 3-4 8-4 8S1 7 1 4a4 4 0 0 1 4-4z" fill="#444"/></svg>Suite 5A, 18 Marlow St Wooloowin QLD 4030 &nbsp;| &nbsp;PO Box 4120 Northgate QLD 4013</div>
  </section>

  <section class="letterhead" aria-label="Letterhead">
    <div class="ring mark"></div>
    <div class="brand-name">Tallowmere Wealth</div>
    <div class="tagline">STRATEGIC FINANCIAL ADVICE</div>
    <div class="ring watermark"></div>

    <div class="lh-contacts">
      <div class="row"><svg viewBox="0 0 12 12"><circle cx="6" cy="6" r="5.3" fill="none" stroke="#444"/><circle cx="6" cy="5" r="2" fill="#444"/></svg>PO Box 4120 Northgate QLD 4013</div>
      <div class="row"><svg viewBox="0 0 12 12"><circle cx="6" cy="6" r="5.3" fill="none" stroke="#444"/><circle cx="6" cy="5" r="2" fill="#444"/></svg>Suite 5A, 18 Marlow St Wooloowin QLD 4030</div>
      <div class="gap"></div>
      <div class="row">
        <svg viewBox="0 0 12 12"><circle cx="6" cy="6" r="5.3" fill="none" stroke="#444"/><path d="M3 5h6v1.5H3z M4.5 6.5h3v2h-3z" fill="#444"/></svg>(07) 3200 5814
        <svg class="sep" viewBox="0 0 12 12"><circle cx="6" cy="6" r="5.3" fill="none" stroke="#444"/><rect x="3.5" y="4.5" width="5" height="3" fill="#444"/></svg>(07) 3200 5815
        <svg class="sep" viewBox="0 0 12 12"><circle cx="6" cy="6" r="5.3" fill="none" stroke="#444"/><rect x="4.5" y="3" width="3" height="6" rx=".5" fill="#444"/></svg>0412 608 273
      </div>
      <div class="row">
        <svg viewBox="0 0 12 12"><circle cx="6" cy="6" r="5.3" fill="none" stroke="#444"/><rect x="3" y="4" width="6" height="4" fill="#444"/></svg>sam@brightvalefinancial.com.au
        <svg class="sep" viewBox="0 0 12 12"><circle cx="6" cy="6" r="5.3" fill="none" stroke="#444"/><circle cx="6" cy="6" r="2.5" fill="none" stroke="#444"/></svg>
      </div>
    </div>

    <svg class="lh-tab" viewBox="0 0 244 30" aria-hidden="true">
      <path d="M0 30 L18 10 Q24 0 40 0 H244 V30 Z" fill="var(--tab)"/>
    </svg>
    <svg style="position:absolute;left:0;top:872px" width="626" height="12" aria-hidden="true">
      <path d="M0 0 H392 L382 12 H0 Z" fill="var(--charcoal)"/>
    </svg>
    <div class="lh-web">www.brightvalefinancial.com.au</div>
  </section>

</div>
</body>
</html>
```